The most modern business card ever !!!

Our company call “Vendalo”. Vendalo is a technology company specialized in cruises solutions. Out main product is a platform to reserve cruises. This is a revolutionary platform that make easier to travel agencies and final users to reserve cruises across dozen companies like tibba, wernu, hpv, dgb, etc..We are a “start up”, with a young team of developers and we want to transmit it.. For it, we want something different, a modern business card that represent cruises and technology.. When someone receive this card, this person should say: wowww this is different… this is modern… this is a cruise related company..
- diferent, modern
- traditions business card

```html
<!DOCTYPE html>
<html lang="en">
<head>
<meta charset="utf-8">
<title>Vendalo — Business Card</title>
<link href="https://fonts.googleapis.com/css2?family=Lato:wght@300;400;700&display=swap" rel="stylesheet">
<style>
  :root {
    --stage: #2b2c2e;
    --card: #1d1f21;
    --accent: #2aa8e0;
    --white: #f4f5f6;
    --muted: #b9bcc0;
    --rule: #6c7075;
    --silver: #c9cbce;
  }
  * { margin: 0; padding: 0; box-sizing: border-box; }
  html, body {
    width: 1200px; height: 1108px; overflow: hidden;
    background: var(--stage);
    font-family: "Lato", Arial, sans-serif;
  }
  .stage {
    position: relative; width: 1200px; height: 1108px;
    display: flex; justify-content: center; align-items: center; gap: 80px;
  }
  .card {
    position: relative; width: 440px; height: 720px;
    border-radius: 30px; background: var(--card);
    box-shadow: 0 18px 40px rgba(0,0,0,.45);
    overflow: hidden;
  }
  .card-front { display: flex; flex-direction: column; align-items: center; }
  .brand-name {
    margin-top: 150px;
    font-size: 96px; font-weight: 400; letter-spacing: 2px;
    color: var(--white); line-height: 1;
  }
  .person { margin-top: 130px; text-align: center; }
  .person-name {
    font-size: 30px; font-weight: 400; color: var(--accent);
    letter-spacing: .5px; text-transform: uppercase;
  }
  .person-role { font-size: 22px; font-weight: 300; color: var(--muted); margin-top: 2px; }
  .divider-icons {
    display: flex; align-items: center; gap: 8px; width: 300px; margin-top: 22px;
  }
  .divider-icons .rule { flex: 1; height: 1px; background: var(--rule); }
  .icon { width: 24px; height: 24px; display: block; }
  .contact { margin-top: 14px; text-align: center; color: var(--white); font-size: 22px; line-height: 1.4; font-weight: 400; }
  .rule-full { width: 300px; height: 1px; background: var(--rule); margin-top: 16px; }
  .address { margin-top: 14px; text-align: center; color: var(--muted); font-size: 22px; line-height: 1.4; }
  .back-texture {
    position: absolute; inset: 0;
    background: linear-gradient(160deg, #232528 0%, #1c1e20 55%, #191a1c 100%);
  }
  .back-brand {
    position: absolute; right: 40px; bottom: 110px;
    font-size: 96px; font-weight: 400; letter-spacing: 2px;
    color: var(--silver); line-height: 1;
  }
</style>
</head>
<body>
<main class="stage">
  <section class="card card-front" aria-label="Business card front">
    <h1 class="brand-name">Vendalo</h1>
    <div class="person">
      <p class="person-name">Elias Marren</p>
      <p class="person-role">Managing Director</p>
    </div>
    <div class="divider-icons">
      <span class="rule"></span>
      <svg class="icon" viewBox="0 0 24 24" aria-label="Phone">
        <circle cx="12" cy="12" r="12" fill="var(--accent)"/>
        <path d="M8.5 6.5c.6-.4 1.2-.2 1.5.4l.9 1.8c.2.5.1 1-.3 1.3l-.8.6c.6 1.4 1.7 2.5 3.1 3.1l.6-.8c.3-.4.8-.5 1.3-.3l1.8.9c.6.3.8.9.4 1.5-.8 1.2-2 1.7-3.3 1.2-2.8-1-5-3.2-6-6-.5-1.3 0-2.5 1.2-3.3z" fill="var(--card)"/>
      </svg>
      <svg class="icon" viewBox="0 0 24 24" aria-label="Email">
        <circle cx="12" cy="12" r="12" fill="var(--accent)"/>
        <rect x="6.5" y="8" width="11" height="8" rx="1" fill="var(--card)"/>
        <path d="M7 8.5l5 4 5-4" fill="none" stroke="var(--accent)" stroke-width="1.2"/>
      </svg>
      <svg class="icon" viewBox="0 0 24 24" aria-label="Website">
        <circle cx="12" cy="12" r="12" fill="var(--accent)"/>
        <circle cx="12" cy="12" r="5.5" fill="none" stroke="var(--card)" stroke-width="1.4"/>
        <ellipse cx="12" cy="12" rx="2.3" ry="5.5" fill="none" stroke="var(--card)" stroke-width="1.2"/>
        <path d="M6.5 12h11" stroke="var(--card)" stroke-width="1.2"/>
      </svg>
      <span class="rule"></span>
    </div>
    <div class="contact">
      <p>312 708 4491</p>
      <p>elias@vendalo.io</p>
      <p>www.vendalo.io</p>
    </div>
    <div class="rule-full"></div>
    <div class="address">
      <p>18, Harbour Quay Road,</p>
      <p>Marisport, 60731</p>
    </div>
  </section>

  <section class="card card-back" aria-label="Business card back">
    <div class="back-texture" role="img" aria-label="Subtle tone-on-tone repeated brand name pattern"></div>
    <p class="back-brand">Vendalo</p>
  </section>
</main>
</body>
</html>
```